Soccer Training for Boys and Girls

I need like a flyer to post on facebook and instagram.
This is what O want to have on it.
you can use any color , soccer field on the background , or any soccer pictures.
Recreational and Travel Teams
Ages :5 to 14 years old
Field: Holloway Crest Middle School (4726 Thistle ln Silver spring, MD 20847)
Register online www.varnelleacademy.example
-passing
-kicking
-shooting
-dribbling
-ball Control
Registration :$210 (includes 1st month, registration, practice Uniform
after 1st month.

Call us Phone:(240)555-0187

Nice to have
• kids playing soccer , soccer fields

```html
<!DOCTYPE html>
<html lang="en">
<head>
<meta charset="utf-8">
<title>Boys and Girls Soccer Training – Social Flyers</title>
<link href="https://fonts.googleapis.com/css2?family=Montserrat:ital,wght@0,300;0,400;0,600;0,700;0,800;1,400;1,700;1,800&display=swap" rel="stylesheet">
<style>
:root{
  --page:#e9e9e9;
  --card:#141414;
  --photo-a:#3a3a3a;
  --photo-b:#1c1c1c;
  --turf:#24381f;
  --ink:#ffffff;
  --muted:#d6d6d6;
  --accent:#ffd21a;
  --accent-deep:#f5b800;
  --crest:#1f3f8f;
}
*{box-sizing:border-box;margin:0;padding:0}
html,body{width:1200px;height:848px;overflow:hidden;background:var(--page)}
body{position:relative;font-family:"Montserrat",Arial,sans-serif;color:var(--ink)}
.card{position:absolute;width:355px;height:355px;background:var(--card);overflow:hidden}
.photo{position:absolute;background:radial-gradient(ellipse at 50% 45%,var(--photo-a),var(--photo-b) 75%)}
.photo::after{content:"";position:absolute;left:0;right:0;bottom:0;height:22%;background:linear-gradient(to bottom,transparent,var(--turf))}
.t{position:absolute;white-space:nowrap;line-height:1}
.c{left:0;width:100%;text-align:center}
.r{right:12px;text-align:right}
.academy{font-size:8px;font-weight:300;color:var(--muted)}
.rule{position:absolute;height:1.5px;width:35px;background:var(--accent)}
.title-top{font-weight:800;letter-spacing:-.3px}
.title-main{font-weight:800;color:var(--accent);letter-spacing:-.3px}
.mixed{letter-spacing:-1px;font-weight:700}
.sub{font-size:8px;font-weight:300;color:var(--muted)}
.label{font-size:13px;font-weight:800;font-style:italic;color:var(--accent)}
.label svg{width:8px;height:9px;margin-right:3px;vertical-align:0}
.detail{font-size:8px;font-style:italic;color:var(--muted)}
.addr{font-size:5px;font-style:italic;color:var(--muted)}
.tick{position:absolute;width:1px;background:var(--muted)}
.skills{font-size:13.5px;font-weight:800;line-height:1.3;white-space:nowrap}
.reg{font-size:7px;font-weight:800;font-style:italic;color:var(--accent);line-height:1.3;white-space:nowrap}
.reg b{font-size:10.5px}
.cta{font-size:7px;font-weight:600}
.band{position:absolute;height:18px;background:linear-gradient(90deg,var(--accent-deep),var(--accent));transform:skewX(-8deg) rotate(-1deg);display:flex;align-items:center;justify-content:center;font-style:italic;font-weight:800;color:var(--ink);white-space:nowrap}
.band.phone{font-size:10.5px}
.band.url{font-size:6.5px;height:17px}
.logo{position:absolute;display:flex;align-items:center;gap:2px;font-size:6.5px;font-weight:700;color:var(--ink)}
.logo i{display:block;width:9px;height:9px;border-radius:50%;background:var(--crest)}
</style>
</head>
<body>

<svg width="0" height="0" style="position:absolute">
  <defs>
    <symbol id="mark" viewBox="0 0 8 9"><path d="M1 1 L7 8 M7 1 L1 8" stroke="#ffffff" stroke-width="1.6" stroke-linecap="round"/></symbol>
  </defs>
</svg>

<!-- Card 1 -->
<section class="card" style="left:40px;top:39px">
  <div class="photo" role="img" aria-label="Player in white kit stepping beside a soccer ball on turf" style="left:0;top:80px;width:175px;height:275px"></div>
  <div class="logo" style="left:307px;top:24px"><i></i>Varnelle</div>
  <div class="t c academy" style="top:11px">Varnelle Soccer Academy</div>
  <div class="t c title-top" style="top:25px;font-size:24px">BOYS &amp; GIRLS</div>
  <div class="t c title-main" style="top:88px;display:none"></div>
  <div class="t c title-main" style="top:52px;font-size:25px">SOCCER TRAINING</div>
  <div class="t c sub" style="top:79px">Recreational and Travel Teams</div>
  <div class="t label" style="left:173px;top:101px"><svg><use href="#mark"/></svg>Ages</div>
  <div class="tick" style="left:177px;top:117px;height:11px"></div>
  <div class="t detail" style="left:185px;top:120px">5 To 14 Years Old</div>
  <div class="t label" style="left:173px;top:142px"><svg><use href="#mark"/></svg>Field</div>
  <div class="tick" style="left:177px;top:158px;height:17px"></div>
  <div class="t detail" style="left:186px;top:162px">Holloway Crest Middle School</div>
  <div class="t addr" style="left:186px;top:173px">4726 Thistle ln Silver Spring, MD 20847</div>
  <div class="t r skills" style="top:194px">Passing, Kicking, Shooting,<br>Dribbling, Ball Control</div>
  <div class="t r reg" style="top:240px">Registration <b>$210</b> (Includes 1st Month,<br>Registration, Practice Uniform)</div>
  <div class="t cta" style="left:220px;width:117px;text-align:center;top:277px">Call Now</div>
  <div class="band phone" style="left:220px;top:288px;width:117px">(240)555-0187</div>
  <div class="t cta" style="left:216px;width:124px;text-align:center;top:315px">Register Online</div>
  <div class="band url" style="left:216px;top:324px;width:124px">www.varnelleacademy.example</div>
</section>

<!-- Card 2 -->
<section class="card" style="left:422px;top:39px">
  <div class="photo" role="img" aria-label="Player's boot resting on a soccer ball on turf" style="left:150px;top:175px;width:205px;height:180px"></div>
  <div class="logo" style="left:299px;top:30px"><i></i>Varnelle</div>
  <div class="t academy" style="left:13px;top:11px">Varnelle Soccer Academy</div>
  <div class="rule" style="left:13px;top:22px;width:55px;height:1px"></div>
  <div class="t title-top mixed" style="left:12px;top:27px;font-size:27px">Boys and Girls</div>
  <div class="t title-main mixed" style="left:12px;top:58px;font-size:28px">Soccer Training</div>
  <div class="rule" style="left:13px;top:89px"></div>
  <div class="t sub" style="left:13px;top:93px">Recreational and Travel Teams</div>
  <div class="t label" style="left:57px;top:128px"><svg><use href="#mark"/></svg>Ages</div>
  <div class="tick" style="left:62px;top:144px;height:11px"></div>
  <div class="t detail" style="left:68px;top:148px">5 To 14 Years Old</div>
  <div class="t label" style="left:167px;top:128px"><svg><use href="#mark"/></svg>Field</div>
  <div class="tick" style="left:172px;top:144px;height:17px"></div>
  <div class="t detail" style="left:178px;top:148px">Holloway Crest Middle School</div>
  <div class="t addr" style="left:178px;top:159px">4726 Thistle ln Silver Spring, MD 20847</div>
  <div class="t skills" style="left:12px;top:185px">Passing, Kicking, Shooting,<br>Dribbling, Ball Control</div>
  <div class="t reg" style="left:13px;top:239px">Registration <b>$210</b> (Includes 1st Month,<br>Registration, Practice Uniform)</div>
  <div class="t cta" style="left:22px;top:279px">Call Now</div>
  <div class="band phone" style="left:13px;top:289px;width:116px">(240)555-0187</div>
  <div class="t cta" style="left:22px;top:315px">Register Online</div>
  <div class="band url" style="left:15px;top:324px;width:125px">www.varnelleacademy.example</div>
</section>

<!-- Card 3 -->
<section class="card" style="left:804px;top:39px">
  <div class="photo" role="img" aria-label="Player in white kit juggling a soccer ball" style="left:236px;top:0;width:119px;height:330px"></div>
  <div class="logo" style="left:305px;top:22px"><i></i>Varnelle</div>
  <div class="t academy" style="left:13px;top:12px">Varnelle Soccer Academy</div>
  <div class="rule" style="left:13px;top:23px;width:55px;height:1px"></div>
  <div class="t title-top mixed" style="left:12px;top:28px;font-size:29px">Boys and Girls</div>
  <div class="t title-main mixed" style="left:12px;top:61px;font-size:30px">Soccer Training</div>
  <div class="t sub" style="left:13px;top:96px">Recreational and Travel Teams</div>
  <div class="t label" style="left:12px;top:125px"><svg><use href="#mark"/></svg>Ages</div>
  <div class="tick" style="left:17px;top:141px;height:11px"></div>
  <div class="t detail" style="left:24px;top:145px">5 To 14 Years Old</div>
  <div class="t label" style="left:12px;top:173px"><svg><use href="#mark"/></svg>Field</div>
  <div class="tick" style="left:17px;top:189px;height:17px"></div>
  <div class="t detail" style="left:25px;top:194px">Holloway Crest Middle School</div>
  <div class="t addr" style="left:25px;top:206px">4726 Thistle ln Silver Spring, MD 20847</div>
  <div class="t skills" style="left:12px;top:223px;line-height:1.25">Passing, Kicking,<br>Shooting, Dribbling,<br>Ball Control</div>
  <div class="t reg" style="left:13px;top:286px;font-size:7.4px">Registration <b>$210</b> (Includes 1st Month, Registration, Practice Uniform)</div>
  <div class="t cta" style="left:13px;width:116px;text-align:center;top:315px">Call Now</div>
  <div class="band phone" style="left:13px;top:325px;width:116px">(240)555-0187</div>
  <div class="t cta" style="left:217px;width:126px;text-align:center;top:315px">Register Online</div>
  <div class="band url" style="left:217px;top:325px;width:126px">www.varnelleacademy.example</div>
</section>

<!-- Card 4 -->
<section class="card" style="left:230px;top:421px">
  <div class="photo" role="img" aria-label="Close view of a boot stepping onto a soccer ball on turf" style="left:60px;top:0;width:240px;height:140px"></div>
  <div class="logo" style="left:300px;top:30px"><i></i>Varnelle</div>
  <div class="t c academy" style="top:129px">Varnelle Soccer Academy</div>
  <div class="t c title-top" style="top:145px;font-size:26px">BOYS &amp; GIRLS</div>
  <div class="t c title-main" style="top:173px;font-size:28px">SOCCER TRAINING</div>
  <div class="t c sub" style="top:205px">Recreational and Travel Teams</div>
  <div class="t label" style="left:57px;top:227px"><svg><use href="#mark"/></svg>Ages</div>
  <div class="tick" style="left:62px;top:243px;height:11px"></div>
  <div class="t detail" style="left:68px;top:247px">5 To 14 Years Old</div>
  <div class="t label" style="left:166px;top:227px"><svg><use href="#mark"/></svg>Field</div>
  <div class="tick" style="left:171px;top:243px;height:17px"></div>
  <div class="t detail" style="left:178px;top:247px">Holloway Crest Middle School</div>
  <div class="t addr" style="left:178px;top:258px">4726 Thistle ln Silver Spring, MD 20847</div>
  <div class="t c skills" style="top:273px;font-size:12.3px">Passing, Kicking, Shooting, Dribbling, Ball Control</div>
  <div class="t c reg" style="top:294px">Registration <b>$210</b> (Includes 1st Month, Registration, Practice Uniform)</div>
  <div class="t cta" style="left:12px;width:117px;text-align:center;top:313px">Call Now</div>
  <div class="band phone" style="left:12px;top:323px;width:117px">(240)555-0187</div>
  <div class="t cta" style="left:217px;width:125px;text-align:center;top:313px">Register Online</div>
  <div class="band url" style="left:217px;top:323px;width:125px">www.varnelleacademy.example</div>
</section>

<!-- Card 5 -->
<section class="card" style="left:614px;top:421px">
  <div class="photo" role="img" aria-label="Player in white kit running with a soccer ball" style="left:0;top:0;width:190px;height:250px"></div>
  <div class="logo" style="left:14px;top:24px"><i></i>Varnelle</div>
  <div class="t r academy" style="top:12px">Varnelle Soccer Academy</div>
  <div class="rule" style="right:12px;top:23px;width:55px;height:1px"></div>
  <div class="t r title-top mixed" style="top:27px;font-size:28px">Boys and Girls</div>
  <div class="t r title-main mixed" style="top:58px;font-size:29px">Soccer Training</div>
  <div class="t r sub" style="top:93px">Recreational and Travel Teams</div>
  <div class="t label" style="left:205px;top:131px"><svg><use href="#mark"/></svg>Ages</div>
  <div class="tick" style="left:210px;top:147px;height:11px"></div>
  <div class="t detail" style="left:217px;top:152px">5 To 14 Years Old</div>
  <div class="t label" style="left:205px;top:180px"><svg><use href="#mark"/></svg>Field</div>
  <div class="tick" style="left:210px;top:196px;height:17px"></div>
  <div class="t detail" style="left:218px;top:201px">Holloway Crest Middle School</div>
  <div class="t addr" style="left:218px;top:212px">4726 Thistle ln Silver Spring, MD 20847</div>
  <div class="t r skills" style="top:240px;font-size:14.5px">Passing, Kicking,<br>Shooting, Dribbling, Ball Control</div>
  <div class="t r reg" style="top:284px;font-size:7.6px">Registration <b>$210</b> (Includes 1st Month, Registration, Practice Uniform)</div>
  <div class="t cta" style="left:13px;width:115px;text-align:center;top:313px">Call Now</div>
  <div class="band phone" style="left:13px;top:323px;width:115px">(240)555-0187</div>
  <div class="t cta" style="left:217px;width:125px;text-align:center;top:313px">Register Online</div>
  <div class="band url" style="left:217px;top:323px;width:125px">www.varnelleacademy.example</div>
</section>

</body>
</html>
```